RTavenor Business Cards & Letterhead

I have a logo but need a design for some new business cards. We are a Design-Build Firm that specializes in the design and construction of commercial projects.
the cards need to be professional. no cartoon stuff.
i would like to have the cards in AI format so I can update the card as needed. Logo is provided.
Our Address is: 4187 Marlowe Ct. Alder Ridge, Oregon 27614

```html
<!DOCTYPE html>
<html lang="en">
<head>
<meta charset="utf-8">
<title>RTavenor Business Cards</title>
<link href="https://fonts.googleapis.com/css2?family=Arimo:wght@400;700&display=swap" rel="stylesheet">
<style>
  :root {
    --stage: #2b2c2e;
    --brand-blue: #0b68a8;
    --brand-blue-deep: #06487a;
    --brand-blue-light: #1580c4;
    --ink-navy: #123a66;
    --ink-grey: #555a60;
    --ink-dark: #2c2f33;
    --card-white: #f4f5f6;
  }
  * { box-sizing: border-box; margin: 0; padding: 0; }
  html, body { width: 1200px; height: 947px; overflow: hidden; }
  body {
    background: var(--stage);
    font-family: "Arimo", Arial, sans-serif;
    position: relative;
  }
  .card {
    position: absolute;
    width: 540px;
    height: 310px;
    border-radius: 22px;
    overflow: hidden;
  }
  /* Back side */
  .card-back {
    left: 40px;
    top: 150px;
    background: radial-gradient(ellipse at 55% 40%, var(--brand-blue-light) 0%, var(--brand-blue) 45%, var(--brand-blue-deep) 100%);
    display: flex;
    align-items: center;
    justify-content: center;
  }
  .wordmark {
    display: flex;
    align-items: center;
    gap: 12px;
    font-weight: 700;
    letter-spacing: 1px;
  }
  .wordmark-square {
    display: block;
    background: currentColor;
  }
  .card-back .wordmark { color: #ffffff; font-size: 52px; }
  .card-back .wordmark-square { width: 38px; height: 38px; }

  /* Front side */
  .card-front {
    left: 620px;
    top: 470px;
    background: var(--card-white);
  }
  .front-wordmark {
    position: absolute;
    right: 30px;
    top: 26px;
    color: var(--ink-navy);
    font-size: 30px;
  }
  .front-wordmark .wordmark-square { width: 22px; height: 22px; }
  .feature-block {
    position: absolute;
    right: 34px;
    top: 82px;
    width: 180px;
    height: 190px;
    border-radius: 10px;
    background: linear-gradient(135deg, var(--brand-blue-light), var(--brand-blue-deep));
  }
  .holder {
    position: absolute;
    left: 32px;
    top: 56px;
  }
  .holder-name {
    color: var(--brand-blue-deep);
    font-size: 28px;
    font-weight: 700;
  }
  .holder-title {
    color: var(--ink-grey);
    font-size: 14px;
    margin-top: 2px;
  }
  .address {
    position: absolute;
    left: 56px;
    top: 164px;
    color: var(--ink-dark);
    font-size: 16px;
    line-height: 20px;
  }
  .contacts {
    position: absolute;
    left: 36px;
    top: 210px;
    list-style: none;
    color: var(--ink-dark);
    font-size: 16px;
    line-height: 20px;
  }
  .contacts li { display: flex; align-items: center; gap: 8px; }
  .contacts svg { width: 13px; height: 13px; fill: var(--brand-blue); flex: none; }
</style>
</head>
<body>

  <section class="card card-back">
    <div class="wordmark"><span class="wordmark-square"></span>RTAVENOR</div>
  </section>

  <section class="card card-front">
    <div class="wordmark front-wordmark"><span class="wordmark-square"></span>RTAVENOR</div>
    <div class="feature-block"></div>

    <div class="holder">
      <p class="holder-name">Martin Hale</p>
      <p class="holder-title">Managing Director</p>
    </div>

    <p class="address">4187 Marlowe Ct. Alder Ridge<br>Oregon 27614</p>

    <ul class="contacts">
      <li><svg viewBox="0 0 16 16"><path d="M3 1l3 3-1.5 2a9 9 0 0 0 5.5 5.5L12 10l3 3-2 2C7 15 1 9 1 3z"/></svg>919-555-0142</li>
      <li><svg viewBox="0 0 16 16"><path d="M4 0h8a1 1 0 0 1 1 1v14a1 1 0 0 1-1 1H4a1 1 0 0 1-1-1V1a1 1 0 0 1 1-1zm1 2v10h6V2z"/></svg>919-555-0187</li>
      <li><svg viewBox="0 0 16 16"><path d="M0 3h16v10H0zm1.5 1.5L8 9l6.5-4.5z"/></svg>info@rtavenor.com</li>
      <li><svg viewBox="0 0 16 16"><circle cx="8" cy="8" r="7.5"/></svg>www.rtavenor.com</li>
    </ul>
  </section>

</body>
</html>
```